Tandem Hearth Works Pty Ltd

We need business cards for a company based in Perth, we install, service and maintain fire equipment.
On the front we want a great design with our logo and a small spot for our full company name, general company email address and office number. On the back we need space for our name, title, mobile number and email address on the back.

Target Market(s)

Facility managers and commercial/industrial building owners/occupiers.

Contact Information for Business Card

Font styles to use
Sans Serif

Requirements
Must have
• Please only submit 5 of your best samples.
Darker tones are preferred.
Nice to have
• We want to use, black, red and grey. Keep it modern and clean.
I've attached the company logo and a sample of a boarder we use on our emergency plans.
Should not have
• No preference. Let the designer choose.

```html
<!DOCTYPE html>
<html lang="en">
<head>
<meta charset="utf-8">
<title>Tandem Hearth Works Pty Ltd — Business Cards</title>
<link rel="stylesheet" href="https://fonts.googleapis.com/css2?family=Arimo:wght@400;700&display=swap">
<style>
  :root {
    --backdrop: #1c1c1c;
    --card-red: #ec1c24;
    --ink-white: #ffffff;
    --rule: rgba(255, 255, 255, 0.85);
  }
  * { box-sizing: border-box; margin: 0; padding: 0; }
  html, body {
    width: 1093px;
    height: 1200px;
    overflow: hidden;
    background: var(--backdrop);
    font-family: "Arimo", Arial, sans-serif;
    color: var(--ink-white);
  }
  .canvas {
    position: relative;
    width: 1093px;
    height: 1200px;
  }
  .card {
    position: absolute;
    left: 264px;
    width: 580px;
    height: 357px;
    background: var(--card-red);
    text-align: center;
  }
  .card--personal { top: 226px; }
  .card--company { top: 620px; }

  .wordmark {
    position: absolute;
    left: 0;
    right: 0;
    font-weight: 700;
    font-size: 60px;
    line-height: 1;
    letter-spacing: 2px;
  }
  .card--personal .wordmark { top: 92px; }
  .card--company .wordmark { top: 80px; }

  .person-name {
    position: absolute;
    top: 215px;
    left: 0; right: 0;
    font-weight: 700;
    font-size: 24px;
    line-height: 1;
  }
  .person-title {
    position: absolute;
    top: 243px;
    left: 0; right: 0;
    font-weight: 400;
    font-size: 19px;
    line-height: 1;
  }
  .divider {
    position: absolute;
    top: 276px;
    left: 209px;
    width: 160px;
    height: 1px;
    background: var(--rule);
  }
  .contact-row {
    position: absolute;
    left: 0; right: 0;
    display: flex;
    justify-content: center;
    align-items: center;
    gap: 14px;
    font-size: 19px;
    line-height: 1;
  }
  .card--personal .contact-row { top: 290px; }
  .card--company .contact-row { top: 304px; font-size: 18px; gap: 20px; }
  .contact-item {
    display: inline-flex;
    align-items: center;
    gap: 6px;
  }
  .contact-item svg { display: block; fill: var(--ink-white); }

  .company-name {
    position: absolute;
    top: 213px;
    left: 0; right: 0;
    font-weight: 700;
    font-size: 25px;
    line-height: 1;
  }
  .company-phone {
    position: absolute;
    top: 255px;
    left: 0; right: 0;
    font-weight: 700;
    font-size: 28px;
    line-height: 1;
  }
</style>
</head>
<body>
<main class="canvas">

  <section class="card card--personal">
    <div class="wordmark">TANDEM</div>
    <h1 class="person-name">MARCUS ELLERY</h1>
    <p class="person-title">Managing Director</p>
    <div class="divider"></div>
    <div class="contact-row">
      <span class="contact-item">
        <svg width="14" height="20" viewBox="0 0 14 20" aria-hidden="true">
          <path d="M2 0h10a2 2 0 0 1 2 2v16a2 2 0 0 1-2 2H2a2 2 0 0 1-2-2V2a2 2 0 0 1 2-2zm0 3v12h10V3zm5 13.2a1.2 1.2 0 1 0 0 2.4a1.2 1.2 0 0 0 0-2.4z"/>
        </svg>
        789.5550.4821
      </span>
      <span class="contact-item">
        <svg width="20" height="14" viewBox="0 0 20 14" aria-hidden="true">
          <path d="M0 0h20v14H0zM1.5 1.5v.6L10 8l8.5-5.9v-.6zm0 2.4v8.6h4.4zm17 0l-4.4 8.6h4.4zM7.2 7.9L3 12.5h14l-4.2-4.6L10 9.9z"/>
        </svg>
        marcus@tandemhw.com
      </span>
    </div>
  </section>

  <section class="card card--company">
    <div class="wordmark">TANDEM</div>
    <h2 class="company-name">TANDEM HEARTH WORKS PTY LTD</h2>
    <p class="company-phone">789.5550.7300</p>
    <div class="contact-row">
      <span class="contact-item">
        <svg width="20" height="14" viewBox="0 0 20 14" aria-hidden="true">
          <path d="M0 0h20v14H0zM1.5 1.5v.6L10 8l8.5-5.9v-.6zm0 2.4v8.6h4.4zm17 0l-4.4 8.6h4.4zM7.2 7.9L3 12.5h14l-4.2-4.6L10 9.9z"/>
        </svg>
        info@tandemhw.com
      </span>
      <span class="contact-item">
        <svg width="17" height="17" viewBox="0 0 20 20" aria-hidden="true">
          <path d="M10 0a10 10 0 1 0 0 20a10 10 0 0 0 0-20zm0 1.8c1.2 0 2.5 1.9 3.1 4.8H6.9C7.5 3.7 8.8 1.8 10 1.8zM6.6 8.4h6.8a17 17 0 0 1 0 3.2H6.6a17 17 0 0 1 0-3.2zM1.9 8.4h2.9a19 19 0 0 0 0 3.2H1.9a8.2 8.2 0 0 1 0-3.2zm13.3 0h2.9a8.2 8.2 0 0 1 0 3.2h-2.9a19 19 0 0 0 0-3.2zM2.6 6.6A8.3 8.3 0 0 1 6.9 2.4c-.6 1.1-1.1 2.5-1.4 4.2zm11.9 0c-.3-1.7-.8-3.1-1.4-4.2a8.3 8.3 0 0 1 4.3 4.2zM6.9 13.4h6.2c-.6 2.9-1.9 4.8-3.1 4.8s-2.5-1.9-3.1-4.8zm-4.3 0h2.9c.3 1.7.8 3.1 1.4 4.2a8.3 8.3 0 0 1-4.3-4.2zm11.9 0h2.9a8.3 8.3 0 0 1-4.3 4.2c.6-1.1 1.1-2.5 1.4-4.2z"/>
        </svg>
        www.tandemhw.com
      </span>
    </div>
  </section>

</main>
</body>
</html>
```